Marketing Flyer for Ashford Hollow Storage Climate Control Units

We are looking for a professional looking Marketing Flyer to advertise for our Climate Control Self Storage Units. Incorporate photos and our LOGO into the marketing flyer. See our website: AshfordHollowstorage.example
Updates

Marketing Flyer for our Self Storage Climate Control Units at Ashford Hollow Storage in Waynesville, NC

Want more designers to have a chance to submit entries.

Target Market(s)

Self Storage Facility Renters

Industry/Entity Type

Self Storage Facility

Font styles to use
Other font styles liked:
• Montserrat Font is what was used for our LOGO and would like to maintain consistency of Font on the Flyer

Colors
0054AA
0677BA
7BADD7
CADEEF
E8F1F8

Requirements
Must have
• Need to have LOGO in the Flyer and photos of the Climate Control Units

```html
<!DOCTYPE html>
<html lang="en">
<head>
<meta charset="utf-8">
<title>Ashford Hollow Storage – Climate Control Flyer</title>
<link href="https://fonts.googleapis.com/css2?family=Montserrat:ital,wght@0,400;0,500;0,600;0,700;0,800;1,500;1,700&display=swap" rel="stylesheet">
<style>
  :root{
    --brand-blue:#0054AA;
    --brand-deep:#123c8c;
    --brand-mid:#0677BA;
    --brand-light:#7BADD7;
    --brand-pale:#CADEEF;
    --brand-mist:#E8F1F8;
    --ink:#2a2a2a;
    --logo-ink:#1f2a6b;
    --page:#eef1f5;
    --white:#ffffff;
  }
  *{box-sizing:border-box;margin:0;padding:0}
  html,body{width:1200px;height:1200px;overflow:hidden;background:var(--page);font-family:"Montserrat",Arial,sans-serif}
  .flyer{position:absolute;left:190px;top:20px;width:820px;height:1160px;background:var(--white);box-shadow:0 6px 24px rgba(0,0,0,.18);overflow:hidden}
  .hero{position:absolute;left:0;top:0;width:820px;height:500px}
  .brand{position:absolute;right:20px;top:40px;width:250px;text-align:center;color:var(--logo-ink);font-weight:700}
  .brand-dot{width:54px;height:54px;border-radius:50%;background:var(--logo-ink);margin:0 auto 16px}
  .brand-name{font-size:21px;letter-spacing:.5px;line-height:1.1;white-space:nowrap}
  .brand-sub{font-size:13px;letter-spacing:5px;margin-top:6px}
  .hero-title{position:absolute;right:24px;top:240px;text-align:right;color:var(--white);font-weight:800;font-size:23px;line-height:1.3;text-transform:uppercase;white-space:nowrap}
  .hero-title-line{display:block}
  .hero-sub{position:absolute;right:24px;top:346px;color:var(--white);font-size:18px;font-weight:500;white-space:nowrap}
  .pill{display:inline-block;background:var(--brand-blue);color:var(--white);font-weight:800;font-size:27px;padding:2px 18px;border-radius:20px;letter-spacing:.5px}
  .who{position:absolute;right:28px;top:478px;text-align:right}
  .who-text{position:absolute;left:200px;right:24px;top:528px;font-size:13.5px;line-height:1.3;color:var(--ink);text-align:right}
  .offer{position:absolute;left:0;right:0;top:612px;text-align:center}
  .offer-text{position:absolute;left:40px;right:40px;top:662px;font-size:13.5px;line-height:1.35;color:var(--ink);text-align:center}
  .features{position:absolute;left:38px;right:38px;top:716px;height:190px;background:#f6f7f9;border-radius:18px;box-shadow:0 6px 10px rgba(0,0,0,.08);display:grid;grid-template-columns:1fr 1fr 1fr;grid-template-rows:1fr 1fr;padding:8px 0}
  .feature{display:flex;flex-direction:column;align-items:center;justify-content:center;gap:8px;font-size:14px;font-weight:600;color:#333;position:relative;text-align:center}
  .feature+.feature:not(:nth-child(4))::before{content:"";position:absolute;left:0;top:38%;height:34%;border-left:1.5px solid #bbb}
  .feature svg{width:28px;height:28px;fill:var(--brand-blue)}
  .reviews{position:absolute;left:0;right:0;top:932px;height:140px;background:linear-gradient(90deg,var(--brand-deep),var(--brand-blue));display:grid;grid-template-columns:1fr 1fr 1fr;gap:24px;padding:16px 24px 14px}
  .review{color:var(--white);font-style:italic;font-size:11px;line-height:1.3;font-weight:500;display:flex;flex-direction:column}
  .stars{margin-top:auto;color:var(--brand-pale);font-style:normal;font-size:13px;letter-spacing:1px}
  .reviewer{font-weight:700;font-size:11px}
  .pledge{position:absolute;left:20px;right:20px;top:1084px;text-align:center;color:var(--brand-blue);font-weight:700;font-size:16.5px;line-height:1.3}
  .footer{position:absolute;left:0;right:0;bottom:0;height:30px;background:var(--brand-deep);border-top:5px solid var(--brand-pale);color:var(--white);text-align:center;font-size:13px;font-weight:600;letter-spacing:2.5px;line-height:25px}
</style>
</head>
<body>
<main class="flyer">
  <svg class="hero" viewBox="0 0 820 500">
    <defs>
      <linearGradient id="blueField" x1="0" y1="0" x2="1" y2="1">
        <stop offset="0" stop-color="#0a4fae"/><stop offset="1" stop-color="#123c8c"/>
      </linearGradient>
      <linearGradient id="buildingPhoto" x1="0" y1="0" x2="0" y2="1">
        <stop offset="0" stop-color="#6fb4ee"/><stop offset=".5" stop-color="#9cc9ef"/><stop offset=".62" stop-color="#8a5a45"/><stop offset="1" stop-color="#b9b4ae"/>
      </linearGradient>
      <linearGradient id="unitsPhoto" x1="0" y1="0" x2="1" y2="0">
        <stop offset="0" stop-color="#d9dce2"/><stop offset=".35" stop-color="#1f47a3"/><stop offset="1" stop-color="#2b55b8"/>
      </linearGradient>
      <linearGradient id="entryPhoto" x1="0" y1="0" x2="0" y2="1">
        <stop offset="0" stop-color="#b86a4f"/><stop offset=".6" stop-color="#7d4e40"/><stop offset="1" stop-color="#c9c3bb"/>
      </linearGradient>
      <linearGradient id="hallPhoto" x1="0" y1="0" x2="1" y2="0">
        <stop offset="0" stop-color="#2548a8"/><stop offset=".5" stop-color="#e6e8ec"/><stop offset="1" stop-color="#2548a8"/>
      </linearGradient>
    </defs>
    <rect x="380" y="0" width="440" height="430" fill="url(#blueField)"/>
    <path d="M0,0 H430 C470,90 470,200 420,300 L0,330 Z" fill="url(#buildingPhoto)" role="img" aria-label="Photo of the storage facility building and sign"/>
    <path d="M380,0 H430 C478,90 478,210 428,305" fill="none" stroke="var(--brand-pale)" stroke-width="10"/>
    <path d="M0,420 C200,390 420,380 560,390 C680,398 760,420 820,450 V440 H0 Z" fill="#fff"/>
    <path d="M300,420 C460,380 640,370 820,440 V420 C650,360 460,370 300,420 Z" fill="var(--brand-pale)"/>
    <path d="M560,0 H820 V185 C760,215 680,225 600,210 C555,200 540,150 548,80 C552,40 556,15 560,0 Z" fill="var(--brand-pale)"/>
    <path d="M575,0 H820 V175 C760,205 690,212 615,198 C572,190 560,150 566,80 C569,40 572,15 575,0 Z" fill="#fff"/>
    <circle cx="118" cy="378" r="122" fill="url(#unitsPhoto)" stroke="#e9edf3" stroke-width="5" role="img" aria-label="Photo of blue roll-up storage unit doors"/>
    <circle cx="288" cy="412" r="88" fill="url(#entryPhoto)" stroke="#e9edf3" stroke-width="5" role="img" aria-label="Photo of the office entrance"/>
    <circle cx="370" cy="285" r="54" fill="url(#hallPhoto)" stroke="#e9edf3" stroke-width="4" role="img" aria-label="Photo of a climate controlled indoor hallway"/>
  </svg>

  <div class="brand">
    <div class="brand-dot"></div>
    <div class="brand-name">ASHFORD HOLLOW</div>
    <div class="brand-sub">STORAGE</div>
  </div>

  <h1 class="hero-title"><span class="hero-title-line">Storage Solutions</span><span class="hero-title-line">with Birchline Storage</span><span class="hero-title-line">Management</span></h1>
  <p class="hero-sub">Climate Control Self Storage Units</p>

  <div class="who"><h2 class="pill">WHO WE ARE</h2></div>
  <p class="who-text">Lorem ipsum dolor sit amet, consectetur adipiscing elit, sed do eiusmod tempor incididunt ut labore et dolore magna aliqua. Quis ipsum suspendisse ultrices gravida. Risus commodo viverra maecenas accumsan lacus vel facilisis.</p>

  <div class="offer"><h2 class="pill">WHAT WE OFFER</h2></div>
  <p class="offer-text">Storage features are designed from scratch and stem from years of industry expertise. We provide a high quality and consistent customer experience you can count on.</p>

  <section class="features">
    <div class="feature"><svg viewBox="0 0 24 24"><path d="M10 3 2 10h3v8h5v-5h2V10h3L10 3zm4 9h8v8h-8z"/></svg>Contactless Rental and Payment</div>
    <div class="feature"><svg viewBox="0 0 24 24"><path d="M10 2a3 3 0 0 1 3 3v9a5 5 0 1 1-6 0V5a3 3 0 0 1 3-3zm0 2a1 1 0 0 0-1 1v10.1a3 3 0 1 0 2 0V5a1 1 0 0 0-1-1z"/></svg>Climate Controlled Units</div>
    <div class="feature"><svg viewBox="0 0 24 24"><path d="M6.6 10.8a15 15 0 0 0 6.6 6.6l2.2-2.2a1 1 0 0 1 1-.25 11.4 11.4 0 0 0 3.6.6 1 1 0 0 1 1 1V20a1 1 0 0 1-1 1A17 17 0 0 1 3 4a1 1 0 0 1 1-1h3.5a1 1 0 0 1 1 1c0 1.25.2 2.450.6 3.6a1 1 0 0 1-.25 1z"/></svg>Phone Support 7 Days a Week</div>
    <div class="feature"><svg viewBox="0 0 24 24"><path d="M2 5h13v4h4l3 4v5h-2a3 3 0 0 1-6 0H9a3 3 0 0 1-6 0H2zm15 6v2h3l-1.5-2zM6 17a1 1 0 1 0 0 2 1 1 0 0 0 0-2zm11 0a1 1 0 1 0 0 2 1 1 0 0 0 0-2z"/></svg>RV / Boat / Vehicle Parking</div>
    <div class="feature"><svg viewBox="0 0 24 24"><path d="M12 2a5 5 0 0 1 5 5v3h1a1 1 0 0 1 1 1v10a1 1 0 0 1-1 1H6a1 1 0 0 1-1-1V11a1 1 0 0 1 1-1h1V7a5 5 0 0 1 5-5zm0 2a3 3 0 0 0-3 3v3h6V7a3 3 0 0 0-3-3z"/></svg>Drive Up Access</div>
    <div class="feature"><svg viewBox="0 0 24 24"><path d="M2 6h3v9h9v3H2zm5 1h6v7H7zm8-3h5v11a3 3 0 1 1-4 2.8l-1 .2z"/></svg>Safe and Secure Locations</div>
  </section>

  <section class="reviews">
    <article class="review">This company was amazing to work with from start to finish! I highly recommend using them! They helped me with what I needed plus more<span class="stars">★★★★★</span><span class="reviewer">by Dana Whitfield</span></article>
    <article class="review">Great storage space! Very friendly staff! I have been renting for 2yrs and they have been awesome! Clean environment and safe!<span class="stars">★★★★★</span><span class="reviewer">by Laura Benton</span></article>
    <article class="review">Great storage facility. It's clean, well lit at night, feels safe, &amp; the units are huge. I love that they're all outdoor units so you can pull right up. No long walks or elevators.<span class="stars">★★★★★</span><span class="reviewer">by Mark Delaney</span></article>
  </section>

  <p class="pledge">Our customers are very important to us. If for any reason you need to cancel your rental or have a complaint, we pledge to do our best to accommodate your needs.</p>

  <footer class="footer">www.birchlinesafestorage.example</footer>
</main>
</body>
</html>
```